sydney wedding photography business needs a business card design

we need a business card design for a sydney based wedding photography and videography business. our business name is :golden hour studio and film. our target clients are 24-35 yrs female. our style is candid, organic, natural, dynamic. we are a team of young photographers and videographers, and help brides to create memories that they will cherish for the rest of their lives. the logo will be provided. we want an elegant design that reflects our style, and also want to give a great impression to our clients that we are one of the best studios in sydney and our brand means quality and premium service.

Target Market(s)

bride to be, 24-35 years old, living in sydney and surrunding areas

Industry/Entity Type

Wedding Photography

Contact Information for Business Card

address: 57 tarrant street, glenmore nsw 2047
mobile: 0431872259
phone: (02) 9163 2408
info@tidewillowstudio.net.au
www.tidewillowstudio.net.au
facebook:tidewillowweddings
instagram:tidewillowweddings

Font styles to use
Serif
Sans Serif

Requirements
Nice to have
• maybe add my slogan"memories beyond eternity" if the layout looks good
Should not have
• no black color, not good idea for wedding biz card

```html
<!DOCTYPE html>
<html lang="en">
<head>
<meta charset="utf-8">
<title>Golden Hour Studio and Film – Business Card</title>
<link rel="stylesheet" href="https://fonts.googleapis.com/css2?family=Questrial&display=swap">
<style>
  :root {
    --backdrop: #e9e4dc;
    --card: #3b322b;
    --gold: #e0ab2e;
    --gold-soft: #cf9d2a;
    --card-ink: #3b322b;
  }
  * { box-sizing: border-box; margin: 0; padding: 0; }
  html, body {
    width: 1200px;
    height: 1189px;
    overflow: hidden;
    background: var(--backdrop);
    font-family: "Questrial", "Century Gothic", sans-serif;
    color: var(--gold);
  }
  .canvas {
    position: relative;
    width: 1200px;
    height: 1189px;
  }
  .card {
    position: absolute;
    left: 190px;
    width: 820px;
    height: 469px;
    background: var(--card);
    box-shadow: 0 14px 34px rgba(60, 45, 30, 0.35);
  }
  .card--front { top: 70px; }
  .card--back { top: 620px; }

  .brand {
    display: flex;
    align-items: center;
    gap: 14px;
  }
  .brand__mark {
    width: 14px;
    height: 14px;
    border-radius: 50%;
    background: var(--gold);
    flex: none;
  }
  .brand__name {
    font-size: 40px;
    letter-spacing: 1px;
    color: var(--gold);
    white-space: nowrap;
  }
  .card--front .brand {
    position: absolute;
    left: 50%;
    top: 50%;
    transform: translate(-50%, -50%);
  }
  .card--back .brand {
    position: absolute;
    left: 60px;
    top: 56px;
  }
  .card--back .brand__name { font-size: 34px; }

  .contact {
    position: absolute;
    left: 400px;
    top: 140px;
    color: var(--gold);
  }
  .contact__name {
    font-size: 26px;
    text-transform: uppercase;
    letter-spacing: 0.5px;
    line-height: 1;
  }
  .contact__role {
    font-size: 19px;
    color: var(--gold-soft);
    margin-top: 3px;
    margin-bottom: 16px;
    line-height: 1.1;
  }
  .contact__list { list-style: none; }
  .contact__item {
    display: flex;
    align-items: center;
    gap: 12px;
    font-size: 18px;
    line-height: 1.5;
    white-space: nowrap;
  }
  .contact__icon {
    width: 20px;
    height: 20px;
    flex: none;
    fill: var(--gold);
    stroke: var(--gold);
  }
  .contact__dot {
    width: 20px;
    height: 20px;
    flex: none;
    display: flex;
    align-items: center;
    justify-content: center;
  }
  .contact__dot::before {
    content: "";
    width: 10px;
    height: 10px;
    border-radius: 50%;
    background: var(--gold);
  }
</style>
</head>
<body>
<main class="canvas">
  <section class="card card--front" aria-label="Card front">
    <div class="brand">
      <span class="brand__mark"></span>
      <span class="brand__name">Golden Hour Studio and Film</span>
    </div>
  </section>

  <section class="card card--back" aria-label="Card back">
    <div class="brand">
      <span class="brand__mark"></span>
      <span class="brand__name">Golden Hour Studio and Film</span>
    </div>

    <div class="contact">
      <p class="contact__name">Mara Ellison</p>
      <p class="contact__role">Manager</p>
      <ul class="contact__list">
        <li class="contact__item">
          <svg class="contact__icon" viewBox="0 0 24 24" aria-hidden="true">
            <rect x="6" y="2" width="12" height="20" rx="2" stroke="none"/>
            <rect x="8" y="5" width="8" height="12" fill="#3b322b" stroke="none"/>
            <circle cx="12" cy="19.3" r="1" fill="#3b322b" stroke="none"/>
          </svg>
          <span>0431 872 259</span>
        </li>
        <li class="contact__item">
          <svg class="contact__icon" viewBox="0 0 24 24" aria-hidden="true">
            <path stroke="none" d="M2 9c0-3 4-5 10-5s10 2 10 5v2h-5V8.5c-1.5-.6-3.2-.9-5-.9s-3.5.3-5 .9V11H2z"/>
            <path stroke="none" d="M6 12l2-3h8l2 3v8H6z"/>
            <circle cx="12" cy="15.5" r="2.2" fill="#3b322b" stroke="none"/>
          </svg>
          <span>(02) 9163 2408</span>
        </li>
        <li class="contact__item">
          <svg class="contact__icon" viewBox="0 0 24 24" aria-hidden="true">
            <rect x="2" y="5" width="20" height="14" stroke="none"/>
            <path d="M2.5 5.5 12 13l9.5-7.5" fill="none" stroke="#3b322b" stroke-width="1.6"/>
          </svg>
          <span>info@tidewillowstudio.net.au</span>
        </li>
        <li class="contact__item">
          <svg class="contact__icon" viewBox="0 0 24 24" aria-hidden="true">
            <circle cx="12" cy="12" r="9.5" fill="none" stroke-width="1.8"/>
            <ellipse cx="12" cy="12" rx="4" ry="9.5" fill="none" stroke-width="1.4"/>
            <path d="M2.5 12h19M4 7h16M4 17h16" fill="none" stroke-width="1.4"/>
          </svg>
          <span>www.tidewillowstudio.net.au</span>
        </li>
        <li class="contact__item">
          <svg class="contact__icon" viewBox="0 0 24 24" aria-hidden="true">
            <path stroke="none" d="M12 2a7 7 0 0 0-7 7c0 5.2 7 13 7 13s7-7.8 7-13a7 7 0 0 0-7-7z"/>
            <circle cx="12" cy="9" r="2.6" fill="#3b322b" stroke="none"/>
          </svg>
          <span>57 tarrant street, glenmore nsw 2047</span>
        </li>
        <li class="contact__item">
          <span class="contact__dot" aria-hidden="true"></span>
          <span>Facebook: tidewillowweddings</span>
        </li>
        <li class="contact__item">
          <span class="contact__dot" aria-hidden="true"></span>
          <span>Instagram: tidewillowweddings</span>
        </li>
      </ul>
    </div>
  </section>
</main>
</body>
</html>
```